IT Company requires new Business Card design.

Over the years we have had a few different business card designs. We are now due for new cards across the board for all staff. We felt this would be a good time to start fresh with a new design. Our traditional card simply had our details on the front, and a list of services on the back. We don't particularly need the list of services, we have had cards where the only thing on the rear of the card was our logo.
Feel free to be creative, we would like our tag line "Complete IT Management" to appear at some point, doesn't necessarily have to be with the logo.
I have attached samples and drafts of various previous cards we have used over the years.

```html
<!DOCTYPE html>
<html lang="en">
<head>
<meta charset="utf-8">
<title>Tarn Networking – Business Card</title>
<link href="https://fonts.googleapis.com/css2?family=Open+Sans:wght@400;600;700;800&display=swap" rel="stylesheet">
<style>
  :root {
    --backdrop: #e9e6e1;
    --card: #ffffff;
    --slate: #5e6d7b;
    --slate-dark: #4f5d6a;
    --ink: #3d4650;
    --shadow: rgba(40, 30, 20, 0.18);
  }
  * { margin: 0; padding: 0; box-sizing: border-box; }
  html, body {
    width: 1200px;
    height: 720px;
    overflow: hidden;
    background: var(--backdrop);
    font-family: "Open Sans", Arial, sans-serif;
    color: var(--ink);
  }
  .stage { position: relative; width: 1200px; height: 720px; }

  .card {
    position: absolute;
    width: 560px;
    height: 320px;
    background: var(--card);
    box-shadow: 0 6px 18px var(--shadow);
  }
  .card--front { left: 50px; top: 60px; }
  .card--back  { left: 590px; top: 340px; }

  .brand-name {
    font-weight: 800;
    color: var(--slate);
    text-transform: uppercase;
    line-height: 0.9;
    letter-spacing: -0.5px;
  }
  .brand-square { background: var(--slate); }

  /* Front */
  .card--front .brand-square {
    position: absolute; left: 40px; top: 46px;
    width: 200px; height: 200px;
  }
  .tagline {
    position: absolute; left: 40px; top: 268px;
    width: 210px;
    white-space: nowrap;
    font-size: 10.5px; font-weight: 600;
    letter-spacing: 2px; color: var(--slate);
    text-transform: uppercase;
  }
  .details { position: absolute; left: 270px; top: 30px; width: 270px; }
  .details .brand-name { font-size: 34px; }
  .details .brand-name span { display: block; font-size: 24px; }
  .person { margin-top: 18px; }
  .person-name { font-size: 16px; font-weight: 700; color: var(--slate-dark); line-height: 1.2; }
  .person-role { font-size: 12.5px; color: var(--ink); }
  .contact-list { list-style: none; margin-top: 6px; }
  .contact-list li {
    display: flex; align-items: center; gap: 8px;
    font-size: 12.5px; line-height: 19px;
  }
  .contact-list svg { width: 12px; height: 12px; fill: var(--slate-dark); flex: none; }
  .address { margin-top: 6px; font-size: 12.5px; line-height: 17px; }

  /* Back */
  .back-lockup {
    position: absolute; left: 86px; top: 92px;
    display: flex; align-items: flex-end; gap: 22px;
  }
  .card--back .brand-square { width: 110px; height: 110px; }
  .card--back .brand-name { font-size: 54px; padding-bottom: 4px; }
  .card--back .brand-name span { display: block; font-size: 38px; }
  .back-web {
    position: absolute; right: 44px; bottom: 32px;
    font-size: 19px; letter-spacing: 1px; color: var(--ink);
  }
</style>
</head>
<body>
<main class="stage">

  <section class="card card--front" aria-label="Card front">
    <div class="brand-square" aria-hidden="true"></div>
    <p class="tagline">Complete IT Management</p>

    <div class="details">
      <p class="brand-name">Tarn<span>Networking</span></p>
      <div class="person">
        <p class="person-name">Marcus Reid</p>
        <p class="person-role">Operation Manager</p>
      </div>
      <ul class="contact-list">
        <li>
          <svg viewBox="0 0 12 12" aria-label="Phone"><path d="M2.4 0.8l2 2.1-1 1.3c.7 1.5 1.9 2.7 3.4 3.4l1.3-1 2.1 2-1.2 1.9C4.6 10.4 1.6 7.4 0.5 2z"/></svg>
          08 9555 0142
        </li>
        <li>
          <svg viewBox="0 0 12 12" aria-label="Mobile"><path d="M3 0h6v12H3zM4 1.5v8h4v-8zM5.5 10.3h1v1h-1z" fill-rule="evenodd"/></svg>
          0400 555 318
        </li>
        <li>
          <svg viewBox="0 0 12 12" aria-label="Fax"><path d="M3 0h6v4H3zM0 4.5h12V10H9.5v2h-7v-2H0zM3.5 8v3h5V8z" fill-rule="evenodd"/></svg>
          08 9555 0142
        </li>
        <li>
          <svg viewBox="0 0 12 12" aria-label="Email"><path d="M0 2h12v8H0zM1 3v.4l5 3.2 5-3.2V3zM1 4.6V9h10V4.6L6 7.8z" fill-rule="evenodd"/></svg>
          marcus@tarnnetworking.com.au
        </li>
        <li>
          <svg viewBox="0 0 12 12" aria-label="Website"><path d="M6 0a6 6 0 110 12A6 6 0 016 0zm0 1.2a4.8 4.8 0 100 9.6 4.8 4.8 0 000-9.6zM1.5 5.4h9v1.2h-9zM5.4 1.2h1.2v9.6H5.4z" fill-rule="evenodd"/></svg>
          www.tarnnetworking.com.au
        </li>
      </ul>
      <p class="address">Unit 4 12 Marlow Way<br>Kestrel Park WA 6999</p>
    </div>
  </section>

  <section class="card card--back" aria-label="Card back">
    <div class="back-lockup">
      <div class="brand-square" aria-hidden="true"></div>
      <p class="brand-name">Tarn<span>Networking</span></p>
    </div>
    <p class="back-web">www.tarnnetworking.com.au</p>
  </section>

</main>
</body>
</html>
```